Android App Design Project

Hi my name is Nadir, and I'm an android developer. I'm searching for a professional designer that can design my app.I have already launched the app and you can find it in the apptrove bazaar.

Main Requirements
- 15 sport icons
- 6 android pages
- Action bar
- Buttons and other icons

You need to do all requirements to submit a design. I need the design in both JPEG format and Photoshop PSD format. If you are interested then please download the PDF file ,it will help you a lot.
The name of the app is "MATCH VIEW Classic" you can find it in Orbix Shelf.

NOTICE: You might read that the Payment is not guaranteed if I'm not happy with the design BUT if you make a good design and you win the contest, then you become my main designer that means if I want to change or add something to the design of the app in the future I return to you "the winner" directly to make the redesign and get paid for it.

Regards.
Skype: Fadi Hamoudi "fadi48"
E-mail: fadinadir@quillpost.net

Industry/Entity Type

Tv

Requirements
Must have
• - 15 sport icons
- 6 android pages
- Action bar
- Buttons and other icons

```html
<!DOCTYPE html>
<html lang="en">
<head>
<meta charset="utf-8">
<title>Match provider</title>
<link rel="stylesheet" href="https://fonts.googleapis.com/css2?family=Ubuntu+Condensed&display=swap">
<style>
  :root {
    --bar-top: #f58a45;
    --bar-bottom: #e0581c;
    --bar-divider: rgba(255,255,255,0.35);
    --bg: #2a2a2a;
    --row-top: #303030;
    --row-bottom: #262626;
    --rule-dark: #161616;
    --rule-light: #3b3b3b;
    --text-light: #ffffff;
    --text-muted: #9c9c9c;
    --accent-orange: #ef6a22;
    --accent-red: #d91c12;
    --accent-green: #3ea21c;
  }
  * { box-sizing: border-box; margin: 0; padding: 0; }
  html, body { width: 817px; height: 1200px; overflow: hidden; background: var(--bg); }
  body { font-family: "Ubuntu Condensed", "Arial Narrow", sans-serif; }
  .screen { width: 817px; height: 1200px; overflow: hidden; position: relative; }

  .action-bar {
    height: 102px;
    background: linear-gradient(var(--bar-top), var(--bar-bottom));
    display: flex; align-items: center; position: relative;
  }
  .action-bar__title { color: var(--text-light); font-size: 44px; padding-left: 26px; flex: 1; }
  .action-bar__btn {
    width: 120px; height: 102px; display: flex; align-items: center; justify-content: center;
    border-left: 2px solid var(--bar-divider);
  }

  .match-row, .provider-row {
    border-top: 3px solid var(--rule-light);
    border-bottom: 3px solid var(--rule-dark);
    background: linear-gradient(var(--row-top), var(--row-bottom));
    padding-left: 26px; position: relative;
  }
  .match-row { height: 168px; padding-top: 34px; }
  .match-row__teams { color: var(--text-light); font-size: 34px; font-weight: bold; line-height: 44px; }
  .match-row__vs { color: var(--accent-orange); font-weight: normal; }
  .match-row__date { color: var(--text-light); font-size: 34px; font-weight: bold; line-height: 44px; }
  .match-row__type {
    position: absolute; right: 24px; top: 68px;
    color: var(--accent-red); font-size: 32px; font-weight: bold;
  }

  .provider-row { height: 188px; padding-top: 66px; }
  .provider-row__name { color: var(--text-muted); font-size: 32px; font-weight: bold; line-height: 36px; }
  .provider-row__status { color: var(--accent-green); font-size: 32px; font-weight: bold; line-height: 36px; }
</style>
</head>
<body>
<div class="screen">
  <header class="action-bar">
    <h1 class="action-bar__title">Matche provider</h1>
    <div class="action-bar__btn" aria-label="Back">
      <svg width="54" height="44" viewBox="0 0 54 44">
        <path d="M2 22 L24 2 L24 14 L52 14 L52 30 L24 30 L24 42 Z" fill="#fff" stroke="#c24a12" stroke-width="2"/>
      </svg>
    </div>
    <div class="action-bar__btn" aria-label="Home">
      <svg width="50" height="50" viewBox="0 0 50 50" fill="none" stroke="#fff" stroke-width="3" stroke-linejoin="round">
        <path d="M4 24 L25 4 L46 24"/>
        <path d="M10 20 V46 H40 V20"/>
        <rect x="20" y="30" width="10" height="16"/>
        <rect x="13" y="24" width="6" height="6"/>
        <rect x="31" y="24" width="6" height="6"/>
      </svg>
    </div>
  </header>

  <section class="match-row">
    <p class="match-row__teams">Austrilia <span class="match-row__vs">vs</span> India</p>
    <p class="match-row__date">21.JAN.2013</p>
    <span class="match-row__type">LEAGUE</span>
  </section>

  <section class="provider-row">
    <p class="provider-row__name">PROVIDER : FLARE</p>
    <p class="provider-row__status">avilable</p>
  </section>
  <section class="provider-row">
    <p class="provider-row__name">PROVIDER : FLARE</p>
    <p class="provider-row__status">avilable</p>
  </section>
  <section class="provider-row">
    <p class="provider-row__name">PROVIDER : FLARE</p>
    <p class="provider-row__status">avilable</p>
  </section>
  <section class="provider-row">
    <p class="provider-row__name">PROVIDER : LINKCAST</p>
    <p class="provider-row__status">avilable</p>
  </section>
  <section class="provider-row">
    <p class="provider-row__name">PROVIDER : FLARE</p>
    <p class="provider-row__status">avilable</p>
  </section>
</div>
</body>
</html>
```